Birchline Septic Solutions

Would like to see some single sided ones but would also like to see some double sided with one sided only being the logo. Owners name is Colin Vandro. Phone number is 555-214-0387
Services are pumping, inspections, installs, and repairs

Contact Information for Business Card

555-241-0387 Colin Vandro Harlow Creek, MT

```html
<!DOCTYPE html>
<html lang="en">
<head>
<meta charset="utf-8">
<title>Birchline Septic Solutions – Business Card</title>
<link rel="stylesheet" href="https://fonts.googleapis.com/css2?family=Poppins:ital,wght@0,300;0,400;0,600;1,700&display=swap">
<style>
  :root {
    --stage: #262626;
    --card: #191919;
    --teal: #2bb8b1;
    --white: #f4f4f4;
    --muted: #d6d6d6;
    --silver: #9a9a9a;
  }
  * { margin: 0; padding: 0; box-sizing: border-box; }
  html, body {
    width: 1200px; height: 900px; overflow: hidden;
    background: var(--stage);
    font-family: "Poppins", sans-serif;
  }
  .canvas { position: relative; width: 1200px; height: 900px; }
  .card {
    position: absolute; left: 250px; width: 700px; height: 400px;
    background: var(--card);
    border-bottom: 3px solid var(--teal);
    box-shadow: 0 12px 30px rgba(0,0,0,.45);
    overflow: hidden;
  }
  .card--front { top: 30px; }
  .card--back { top: 470px; }

  .owner { position: absolute; left: 60px; top: 64px; }
  .owner__name {
    color: var(--teal); font-weight: 700; font-style: italic;
    font-size: 26px; letter-spacing: .5px; text-transform: uppercase; line-height: 1.1;
  }
  .owner__title { color: var(--muted); font-weight: 300; font-size: 17px; margin-top: 2px; }

  .wordmark { display: flex; align-items: center; gap: 14px; }
  .wordmark__square { width: 16px; height: 16px; background: var(--teal); flex: none; }
  .wordmark__name {
    font-weight: 600; text-transform: uppercase; line-height: 1.05;
    color: var(--white);
  }
  .wordmark__name span { display: block; }
  .wordmark__main { font-size: 52px; letter-spacing: 1px; }
  .wordmark__sub { font-size: 17px; letter-spacing: 7px; margin-top: 6px; }

  .card--front .wordmark { position: absolute; right: 50px; top: 120px; }

  .contact { position: absolute; left: 300px; top: 268px; list-style: none; }
  .contact__item {
    display: flex; align-items: center; gap: 10px;
    color: var(--white); font-size: 16px; line-height: 27px;
  }
  .contact__icon { width: 15px; height: 15px; flex: none; }

  .card--back .wordmark {
    position: absolute; left: 50%; top: 50%; transform: translate(-50%, -50%);
  }
  .card--back .wordmark__name { color: var(--silver); }
  .card--back .wordmark__main { font-size: 64px; }
  .card--back .wordmark__sub { font-size: 20px; letter-spacing: 9px; }
  .card--back .wordmark__square { background: var(--silver); width: 20px; height: 20px; }
</style>
</head>
<body>
<main class="canvas">

  <section class="card card--front" aria-label="Card front">
    <div class="owner">
      <p class="owner__name">Colin Vandro</p>
      <p class="owner__title">Founder / CEO</p>
    </div>

    <div class="wordmark">
      <span class="wordmark__square"></span>
      <p class="wordmark__name"><span class="wordmark__main">Birchline</span><span class="wordmark__sub">Septic Solutions</span></p>
    </div>

    <ul class="contact">
      <li class="contact__item">
        <svg class="contact__icon" viewBox="0 0 16 16"><path fill="var(--teal)" d="M3.6 1.2l2.3 2.6-1.3 1.8c.8 1.9 2.300 3.4 4.2 4.3l1.8-1.3 2.6 2.3-1.3 2.2c-.4.6-1.1.8-1.8.6C6.2 12.5 3.5 9.8 2.3 5.9c-.2-.7 0-1.4.6-1.8z"/></svg>
        555-241-0387
      </li>
      <li class="contact__item">
        <svg class="contact__icon" viewBox="0 0 16 16"><path fill="var(--teal)" d="M1 3h14v10H1z"/><path fill="none" stroke="var(--card)" stroke-width="1.4" d="M1.5 3.6L8 9l6.5-5.4"/></svg>
        info@birchlineseptic.com
      </li>
      <li class="contact__item">
        <svg class="contact__icon" viewBox="0 0 16 16"><circle cx="8" cy="8" r="7" fill="var(--teal)"/><path fill="none" stroke="var(--card)" stroke-width="1.1" d="M1 8h14M8 1c-2.6 2.6-2.6 11.4 0 14M8 1c2.6 2.6 2.6 11.4 0 14"/></svg>
        www.birchlineseptic.com
      </li>
      <li class="contact__item">
        <svg class="contact__icon" viewBox="0 0 16 16"><path fill="var(--teal)" d="M8 1a5 5 0 0 1 5 5c0 3.6-5 9-5 9S3 9.6 3 6a5 5 0 0 1 5-5z"/><circle cx="8" cy="6" r="1.8" fill="var(--card)"/></svg>
        Harlow Creek, MT
      </li>
    </ul>
  </section>

  <section class="card card--back" aria-label="Card back">
    <div class="wordmark">
      <span class="wordmark__square"></span>
      <p class="wordmark__name"><span class="wordmark__main">Birchline</span><span class="wordmark__sub">Septic Solutions</span></p>
    </div>
  </section>

</main>
</body>
</html>
```